real esate business card with company logo and name

we need a business card design for a real esate company

The company name is Walsh & Brand Pty Ltd, and we have our logo designed and will upload. We want classic or moden feel. Black or white background. looks more textured. Should include folowinginformations
Owen Walsh and Lucy Brand
Sales Agents & Onsite Manager
p: 07 5948 2063
F: 07 5948 2174
M:0431 857 219
3/42 Marlow Crescent, FERNLEA QLD 4213

We want this business card looks professonal. Thank you in advance.

Industry/Entity Type

Real Estate Agent

Contact Information for Business Card

Owen Walsh and Lucy Brand
Onsite Manager & Sales Agents
p: 07 5948 2063
M:0431 857 219

Font styles to use
Serif

Colors
000000
fbfbfb
333333
959595

Requirements
Must have
• company logo and name, black or white back ground

```html
<!DOCTYPE html>
<html lang="en">
<head>
<meta charset="utf-8">
<title>Walsh &amp; Brand Pty Ltd — Business Card</title>
<link rel="stylesheet" href="https://fonts.googleapis.com/css2?family=Oswald:wght@400&family=PT+Sans:wght@400&family=Michroma&display=swap">
<style>
  :root {
    --page-bg: #e4e2df;
    --card-dark: #1c1c1e;
    --card-mid: #333333;
    --card-frost: #bdbab6;
    --card-frost-light: #d6d3cf;
    --text-light: #fbfbfb;
    --text-soft: #d9d9d9;
    --text-grey: #959595;
    --accent-rose: #c9a49a;
    --mark-ink: #333333;
  }
  * { margin: 0; padding: 0; box-sizing: border-box; }
  html, body {
    width: 1200px; height: 969px; overflow: hidden;
    background: var(--page-bg);
  }
  .canvas {
    position: relative; width: 1200px; height: 969px;
  }
  .card {
    position: absolute; left: 100px; top: 200px;
    width: 1000px; height: 568px;
    overflow: hidden;
    border: 1px solid rgba(255,255,255,0.6);
    background:
      linear-gradient(90deg,
        var(--card-dark) 0%,
        #262628 30%,
        var(--card-mid) 45%,
        rgba(110,108,106,0.95) 55%,
        var(--card-frost) 68%,
        var(--card-frost-light) 100%);
    box-shadow: 0 20px 50px rgba(0,0,0,0.18);
  }
  .card::after {
    content: ""; position: absolute; inset: 0;
    background:
      radial-gradient(ellipse at 20% 10%, rgba(255,255,255,0.08), transparent 55%),
      radial-gradient(ellipse at 75% 80%, rgba(0,0,0,0.08), transparent 60%);
    pointer-events: none;
  }
  .contact {
    position: absolute; left: 42px; top: 138px;
    color: var(--text-soft);
    font-family: "PT Sans", sans-serif;
  }
  .contact__names {
    font-family: "Oswald", sans-serif;
    font-size: 31px; font-weight: 400;
    color: var(--text-light); letter-spacing: 0.3px;
    line-height: 1.1;
  }
  .contact__role {
    font-size: 23px; margin-top: 8px; color: var(--text-light);
  }
  .contact__lines {
    list-style: none; margin-top: 26px;
  }
  .contact__line {
    display: flex; align-items: center; gap: 14px;
    font-size: 22px; height: 38px;
  }
  .contact__icon { width: 22px; height: 22px; fill: var(--text-soft); flex: none; }
  .contact__address {
    margin-top: 26px; font-size: 22px; line-height: 33px;
    color: var(--text-soft);
  }
  .company-name {
    position: absolute; left: 42px; top: 487px;
    font-family: "Michroma", sans-serif;
    font-size: 26px; letter-spacing: 1.5px;
    color: var(--accent-rose);
  }
  .brand-block {
    position: absolute; left: 470px; top: 110px;
    width: 470px; height: 340px;
    display: flex; flex-direction: column; align-items: center; justify-content: center;
    gap: 34px;
  }
  .brand-block__square {
    width: 150px; height: 150px;
    border: 22px solid var(--mark-ink);
  }
  .brand-block__name {
    font-family: "Michroma", sans-serif;
    font-size: 30px; letter-spacing: 2px;
    color: var(--mark-ink);
  }
</style>
</head>
<body>
<main class="canvas">
  <section class="card" aria-label="Walsh &amp; Brand business card">
    <div class="contact">
      <h1 class="contact__names">Owen Walsh &amp; Lucy Brand</h1>
      <p class="contact__role">Sales Agents &amp; Onsite Manager</p>
      <ul class="contact__lines">
        <li class="contact__line">
          <svg class="contact__icon" viewBox="0 0 24 24" aria-hidden="true"><path d="M6.6 10.8a15.1 15.1 0 0 0 6.6 6.6l2.2-2.2a1 1 0 0 1 1-.25 11.4 11.4 0 0 0 3.6.57 1 1 0 0 1 1 1V20a1 1 0 0 1-1 1A17 17 0 0 1 3 4a1 1 0 0 1 1-1h3.5a1 1 0 0 1 1 1c0 1.25.2 2.45.57 3.6a1 1 0 0 1-.25 1z"/></svg>
          <span>07 5948 2063</span>
        </li>
        <li class="contact__line">
          <svg class="contact__icon" viewBox="0 0 24 24" aria-hidden="true"><path d="M7 1h10a2 2 0 0 1 2 2v18a2 2 0 0 1-2 2H7a2 2 0 0 1-2-2V3a2 2 0 0 1 2-2zm0 3v14h10V4zm5 15.2a1.2 1.2 0 1 0 0 2.4 1.2 1.2 0 0 0 0-2.4z"/></svg>
          <span>0431 857 219</span>
        </li>
        <li class="contact__line">
          <svg class="contact__icon" viewBox="0 0 24 24" aria-hidden="true"><path d="M7 2h10v5H7zM4 8h16a2 2 0 0 1 2 2v7h-4v5H6v-5H2v-7a2 2 0 0 1 2-2zm4 8v4h8v-4zm10-6a1 1 0 1 0 0 2 1 1 0 0 0 0-2z"/></svg>
          <span>07 5948 2174</span>
        </li>
      </ul>
      <address class="contact__address" style="font-style:normal">
        3/42 Marlow Crescent<br>FERNLEA QLD 4213
      </address>
    </div>
    <p class="company-name">WALSH &amp; BRAND PTY LTD.</p>
    <div class="brand-block">
      <div class="brand-block__square" aria-hidden="true"></div>
      <p class="brand-block__name">WALSH &amp; BRAND</p>
    </div>
  </section>
</main>
</body>
</html>
```